Tolbek cards

I want a simple business card that pops.
Logo on one side.
On side two i want.
"Are you thinking about a new building on your property, or renovating an existing structure? Contact".....
Owners Name: Dale Whitacre
Owners Phone number: 610-555-0187
Address:4076 Copper Ridge RD, Ashgrove, PA 16021
Committed to Quality, Service, and Integrity

```html
<!DOCTYPE html>
<html lang="en">
<head>
<meta charset="utf-8">
<title>Tolbek Builders LLC – Business Cards</title>
<link href="https://fonts.googleapis.com/css2?family=Roboto:wght@400;500;700;900&display=swap" rel="stylesheet">
<style>
  :root {
    --backdrop: #232323;
    --card-brown: #3f2b1a;
    --band-mid: #46301d;
    --band-low: #3a2716;
    --pattern-dark: #3b2817;
    --pattern-light: #6e5131;
    --bronze: #a8744a;
    --text-light: #ffffff;
  }
  * { margin: 0; padding: 0; box-sizing: border-box; }
  html, body {
    width: 1200px; height: 800px; overflow: hidden;
    background: var(--backdrop);
    font-family: "Roboto", Arial, sans-serif;
  }
  .stage {
    position: relative; width: 1200px; height: 800px;
    display: flex; justify-content: center; align-items: center; gap: 60px;
  }
  .card {
    position: relative; width: 340px; height: 595px;
    border-radius: 22px; overflow: hidden;
    background: var(--card-brown);
    box-shadow: 0 18px 40px rgba(0,0,0,.55);
  }
  /* Logo side */
  .card--front .pattern {
    position: absolute; inset: 0;
    background: linear-gradient(160deg, var(--pattern-light) 0%, var(--pattern-dark) 55%, var(--pattern-light) 100%);
  }
  .card--front .brand {
    position: absolute; inset: 0;
    display: flex; flex-direction: column; justify-content: center; align-items: center; gap: 14px;
  }
  .brand-dot { width: 26px; height: 26px; border-radius: 50%; background: var(--text-light); }
  .brand-name {
    font-weight: 900; font-size: 40px; letter-spacing: 2px;
    color: var(--text-light); text-transform: uppercase; text-align: center; line-height: 1.05;
  }
  .brand-name small { display: block; font-size: 16px; letter-spacing: 4px; }
  /* Contact side */
  .bands { position: absolute; inset: 0; }
  .card--back .content {
    position: absolute; inset: 0; color: var(--text-light); text-align: center;
  }
  .back-brand {
    position: absolute; top: 58px; left: 0; right: 0;
    display: flex; flex-direction: column; align-items: center; gap: 10px;
  }
  .back-brand .brand-dot { background: var(--bronze); width: 22px; height: 22px; }
  .back-brand .brand-name { color: var(--bronze); font-size: 36px; }
  .back-brand .brand-name small { font-size: 14px; }
  .owner { position: absolute; top: 195px; left: 0; right: 0; }
  .owner-name { font-size: 30px; font-weight: 700; }
  .owner-role { font-size: 15px; font-weight: 400; margin-top: 2px; }
  .contact-icons { display: flex; justify-content: center; gap: 10px; margin-top: 12px; }
  .contact-icons span {
    width: 26px; height: 26px; border-radius: 50%; background: var(--text-light);
    display: flex; align-items: center; justify-content: center;
  }
  .phone { font-size: 15px; font-weight: 500; margin-top: 12px; }
  .address { font-size: 14px; font-weight: 500; margin-top: 6px; }
  .tagline {
    display: inline-block; margin-top: 16px; padding: 6px 14px;
    border: 2px solid var(--text-light); border-radius: 5px;
    font-size: 14px; font-weight: 500; line-height: 1.3;
  }
  .pitch {
    position: absolute; bottom: 48px; left: 26px; right: 26px;
    font-size: 14px; font-weight: 500; line-height: 1.4;
  }
</style>
</head>
<body>
<main class="stage">
  <section class="card card--front" aria-label="Logo side">
    <div class="pattern" role="img" aria-label="Repeating brand-mark pattern in bronze and brown tones"></div>
    <div class="brand">
      <span class="brand-dot"></span>
      <p class="brand-name">Tolbek<small>Builders LLC</small></p>
    </div>
  </section>

  <section class="card card--back" aria-label="Contact side">
    <svg class="bands" width="340" height="595" viewBox="0 0 340 595" aria-hidden="true">
      <path d="M0 440 C90 470 250 450 340 330 L340 595 L0 595 Z" fill="var(--band-mid)"/>
      <path d="M0 470 C120 480 240 440 340 390 L340 595 L0 595 Z" fill="var(--band-low)"/>
      <path d="M0 500 C80 490 170 470 260 440 L340 420 L340 595 L0 595 Z" fill="var(--card-brown)"/>
    </svg>
    <div class="content">
      <div class="back-brand">
        <span class="brand-dot"></span>
        <p class="brand-name">Tolbek<small>Builders LLC</small></p>
      </div>
      <div class="owner">
        <h1 class="owner-name">Dale Whitacre</h1>
        <p class="owner-role">Owners</p>
        <div class="contact-icons">
          <span>
            <svg width="14" height="14" viewBox="0 0 24 24" aria-label="Phone"><path fill="#3f2b1a" d="M6.6 10.8a15 15 0 0 0 6.6 6.6l2.2-2.2c.3-.3.7-.4 1-.2 1.1.4 2.3.6 3.6.6.6 0 1 .4 1 1V20c0 .6-.4 1-1 1A17 17 0 0 1 3 4c0-.6.4-1 1-1h3.5c.6 0 1 .4 1 1 0 1.3.2 2.5.6 3.6.1.3 0 .7-.2 1z"/></svg>
          </span>
          <span>
            <svg width="14" height="14" viewBox="0 0 24 24" aria-label="Location"><path fill="#3f2b1a" d="M12 2a7 7 0 0 0-7 7c0 5.2 7 13 7 13s7-7.8 7-13a7 7 0 0 0-7-7zm0 9.5A2.5 2.5 0 1 1 12 6.5a2.5 2.5 0 0 1 0 5z"/></svg>
          </span>
        </div>
        <p class="phone">610-555-0187</p>
        <p class="address">4076 Copper Ridge RD, Ashgrove, PA 16021</p>
        <p class="tagline">Committed to Quality,<br>Service, and Integrity</p>
      </div>
      <p class="pitch">"Are you thinking about a new building on your property, or renovating an existing structure? Contact" .....</p>
    </div>
  </section>
</main>
</body>
</html>
```